Flyer for the Lumen 2025 Conference

I am looking to produce a flyer for our upcoming conference, Lumen 2025. This is an annual conference that we plan to publicize on social media. The ideal designer will create a flyer that is eye-catching and effectively communicates the key information. Please see attached our logo, speaker photo, and flyer content.

Target Market(s)

All demographics

Industry/Entity Type

Christian

Font styles to use
Sans Serif

Requirements
Should not have
• Cross, church

```html
<!DOCTYPE html>
<html lang="en">
<head>
<meta charset="utf-8">
<title>Lumen 2025 – The Voice of the Lord</title>
<link rel="stylesheet" href="https://fonts.googleapis.com/css2?family=Bebas+Neue&family=Cinzel:wght@500&family=Montserrat:wght@500&family=Poppins:wght@400;500;600;700&display=swap">
<style>
  :root{
    --stage:#8c8c8c;
    --blue:#1f5683;
    --blue-dark:#12365a;
    --navy:#0f3a63;
    --orange:#f7941d;
    --orange-deep:#e07f10;
    --white:#ffffff;
  }
  *{margin:0;padding:0;box-sizing:border-box}
  html,body{width:869px;height:1200px;overflow:hidden;background:var(--stage)}
  .flyer{
    position:absolute;left:107px;top:109px;width:655px;height:982px;overflow:hidden;
    background:radial-gradient(ellipse at 50% 45%, #2a6494 0%, var(--blue) 45%, var(--blue-dark) 100%);
    font-family:'Poppins',sans-serif;color:var(--white);
  }
  .abs{position:absolute}
  .event-name{left:0;width:100%;top:22px;text-align:center;font-family:'Montserrat',sans-serif;font-weight:500;font-size:28px;letter-spacing:1px;line-height:1.2}
  .event-type{left:0;width:100%;top:54px;text-align:center;font-family:'Cinzel',serif;font-weight:500;font-size:29px;letter-spacing:1px}
  .title{left:28px;top:108px}
  .title text{font-family:'Bebas Neue',sans-serif;fill:var(--orange)}

  .date-card{left:29px;width:127px;height:177px;border:1.5px solid var(--white);text-align:center;font-family:'Bebas Neue',sans-serif;line-height:1}
  .date-card .month{display:block;margin-top:7px;font-size:35px}
  .date-card .day-num{display:block;font-size:68px;margin-top:-3px}
  .date-card .weekday{display:block;font-size:44px;margin-top:-6px;letter-spacing:-.5px}
  .date-card .weekday.long{font-size:36px;margin-top:0}
  .date-card .time{position:absolute;left:9px;right:9px;bottom:6px;height:24px;background:var(--orange);font-size:19px;line-height:25px}
  .card-1{top:224px}.card-2{top:413px}.card-3{top:601px}

  .halo{left:245px;top:262px;width:306px;height:306px;border-radius:50%;background:rgba(140,175,205,.35)}
  .sun{left:258px;top:275px;width:280px;height:280px;border-radius:50%;background:var(--orange);border:6px solid var(--orange-deep)}
  .speaker-photo{left:272px;top:209px;width:252px;height:336px;border-radius:120px 120px 30px 30px;
    background:linear-gradient(180deg,#2d6fc4 0%,#1f5bb0 55%,#1a4c94 100%)}
  .speaker-label{left:0;width:796px;top:580px;text-align:center;font-family:'Bebas Neue',sans-serif;font-size:38px;color:var(--orange);line-height:1}
  .speaker-name{left:0;width:796px;top:613px;text-align:center;font-size:17px;font-weight:400}

  .info-panel{left:178px;top:656px;width:445px;height:119px;background:var(--white);color:var(--navy)}
  .location-title{left:13px;top:16px;font-size:20px;font-weight:700;color:var(--orange);letter-spacing:.5px}
  .location-address{left:14px;top:48px;font-size:11.5px;font-weight:600;line-height:17px}
  .panel-divider{left:252px;top:6px;width:1.5px;height:107px;background:var(--orange)}
  .app-call{left:262px;top:10px;width:177px;text-align:center}
  .app-call .lead{display:block;font-size:19px;font-weight:700;line-height:22px}
  .app-call .app-name{display:block;font-size:26px;font-weight:700;color:var(--orange);line-height:26px}
  .app-call .note{display:block;font-size:11px;font-weight:400;margin-top:1px}
  .store-badge{top:80px;width:79px;height:26px;border-radius:4px;background:#111;border:1px solid #999}
  .badge-1{left:269px}.badge-2{left:352px}

  .edge{left:0;top:790px;width:100%;height:90px;background:linear-gradient(180deg,rgba(255,255,255,0) 0%,rgba(230,238,245,.6) 50%,var(--white) 100%)}
  .footer{left:0;top:870px;width:100%;height:112px;background:var(--white);color:var(--navy)}
  .brand{left:58px;top:44px;font-size:30px;font-weight:600;color:var(--navy);letter-spacing:1px;line-height:1}
  .footer-divider{left:251px;top:18px;width:1.5px;height:87px;background:var(--orange)}
  .phone-icon{left:310px;top:22px}
  .phone{left:341px;top:8px;font-size:38px;font-weight:700;letter-spacing:.5px;line-height:1.2}
  .contact-row{top:66px;font-size:11.3px;font-weight:700}
  .mail-icon{left:309px;top:67px}
  .email{left:341px}
  .globe-icon{left:476px;top:64px}
  .web{left:507px}
</style>
</head>
<body>
<main class="flyer">
  <p class="abs event-name">LUMEN 2025</p>
  <p class="abs event-type">A PROPHETIC CONFERENCE</p>
  <svg class="abs title" width="615" height="72" viewBox="0 0 615 72" aria-label="The Voice of the Lord">
    <text x="0" y="68" font-size="92" textLength="610" lengthAdjust="spacingAndGlyphs">THE VOICE OF THE LORD</text>
  </svg>

  <section class="abs date-card card-1"><span class="month">December</span><span class="day-num">26</span><span class="weekday">Friday</span><span class="time">6:30PM - 9:00PM</span></section>
  <section class="abs date-card card-2"><span class="month">December</span><span class="day-num">27</span><span class="weekday long">Saturday</span><span class="time">5:30PM - 8:00PM</span></section>
  <section class="abs date-card card-3"><span class="month">December</span><span class="day-num">28</span><span class="weekday">Sunday</span><span class="time">4:30PM - 7:00PM</span></section>

  <div class="abs halo"></div>
  <div class="abs sun"></div>
  <div class="abs speaker-photo" role="img" aria-label="Photo of the speaker seated, wearing a blue suit"></div>
  <p class="abs speaker-label">SPEAKER</p>
  <p class="abs speaker-name">PROPHET ELIAS MORENO</p>

  <section class="abs info-panel">
    <h2 class="abs location-title">LOCATION</h2>
    <p class="abs location-address">The Harborview Performing Arts Center<br>218 Linden Avenue Brookhaven,<br>Maine 04110</p>
    <div class="abs panel-divider"></div>
    <p class="abs app-call"><span class="lead">DOWNLOAD THE</span><span class="app-name">VESTRA APP</span><span class="note">to stay updated on the event</span></p>
    <div class="abs store-badge badge-1"></div>
    <div class="abs store-badge badge-2"></div>
  </section>

  <div class="abs edge"></div>
  <footer class="abs footer">
    <p class="abs brand">VESTRA</p>
    <div class="abs footer-divider"></div>
    <svg class="abs phone-icon" width="20" height="20" viewBox="0 0 24 24" aria-hidden="true">
      <path d="M6.6 10.8a15 15 0 0 0 6.6 6.6l2.2-2.2c.3-.3.7-.4 1-.2 1.1.4 2.3.6 3.6.6.6 0 1 .4 1 1V20c0 .6-.4 1-1 1A17 17 0 0 1 3 4c0-.6.4-1 1-1h3.5c.6 0 1 .4 1 1 0 1.3.2 2.5.6 3.6.1.3 0 .7-.2 1z" fill="none" stroke="#f7941d" stroke-width="2"/>
    </svg>
    <p class="abs phone">207 555 0148</p>
    <svg class="abs mail-icon" width="19" height="13" viewBox="0 0 19 13" aria-hidden="true">
      <rect x="1" y="1" width="17" height="11" fill="none" stroke="#f7941d" stroke-width="1.6"/>
      <path d="M1 1l8.5 6.5L18 1" fill="none" stroke="#f7941d" stroke-width="1.6"/>
    </svg>
    <p class="abs contact-row email">contact@vestra.org</p>
    <svg class="abs globe-icon" width="19" height="19" viewBox="0 0 20 20" aria-hidden="true">
      <g fill="none" stroke="#f7941d" stroke-width="1.4"><circle cx="10" cy="10" r="8.5"/><ellipse cx="10" cy="10" rx="3.8" ry="8.5"/><path d="M1.5 10h17M3 5.5h14M3 14.5h14"/></g>
    </svg>
    <p class="abs contact-row web">www.vestra.org</p>
  </footer>
</main>
</body>
</html>
```